AI Business Tools Landing Page

My web-based website builder (Pavlora.com) will be adding many new features in the very near future and I need an eye-catching landing page to promote these new products.

The page will have a primary section of the 8 main products we are promoting:
1. AI Instant Website Generator
2. AI Chatbot
3. Online Store Builder with AI Assistance
4. AI Auto-Blogging System
5. Online Scheduling System
6. Custom Email System
7. SEO Service
8. CRM System

The page will also have a smaller section for links to our affiliate programs. These can be smaller, less-promanent buttons or links. These are the affiliate products:
1. Get Your LLC
2. Website Design and Maintenance
3. Search Ads Management
4. Social Media Posting Service
5. Logo Design
6. Trademark Registration
7. Patent Application
8. Printing Services (including postcards, flyers, and merch.)
9. Bulk AI Content Generator

The theme and color scheme of the page should follow the theme of our main website, which is https://pavlora.com.

I need the page fully coded and ready to deploy on my server.

I look forward to seeing your amazing designs!

```html
<!DOCTYPE html>
<html lang="en">
<head>
<meta charset="utf-8">
<title>Pavlora – AI Business Tools</title>
<link rel="stylesheet" href="https://fonts.googleapis.com/css2?family=Fira+Sans:wght@600;700&family=Open+Sans:wght@400;600&display=swap">
<style>
  :root{
    --navy:#0a2151;
    --navy-deep:#071a40;
    --navy-light:#1b4a92;
    --footer:#0b1735;
    --cyan:#2fc3ec;
    --cyan-strong:#1f9fe6;
    --card-fill:#045a8b;
    --white:#ffffff;
    --line:rgba(255,255,255,.6);
    --muted:#dce8f7;
  }
  *{box-sizing:border-box;margin:0;padding:0}
  html,body{width:724px;height:1200px;overflow:hidden}
  body{
    position:relative;
    font-family:"Open Sans",Arial,sans-serif;
    color:var(--white);
    background:
      radial-gradient(ellipse 420px 300px at 0 60px, rgba(46,110,200,.55), transparent 70%),
      radial-gradient(ellipse 300px 240px at 724px 40px, rgba(40,100,190,.45), transparent 70%),
      radial-gradient(ellipse 380px 260px at 0 800px, rgba(40,95,180,.35), transparent 70%),
      linear-gradient(180deg,#0c2a62 0%,var(--navy) 35%,var(--navy-deep) 100%);
  }
  .abs{position:absolute}
  .heading{font-family:"Fira Sans",Arial,sans-serif;font-weight:700}
  .accent{color:var(--cyan)}

  /* brand */
  .brand{display:flex;align-items:center;gap:8px;font-family:"Fira Sans",Arial,sans-serif;font-weight:600;color:var(--white)}
  .brand-mark{width:26px;height:26px;border-radius:50%;background:var(--cyan)}
  .brand--top{left:0;right:0;top:33px;justify-content:center;font-size:23px}
  .brand--footer{left:88px;top:1148px;font-size:22px}

  /* hero */
  .hero-title{left:0;right:0;top:103px;text-align:center;font-size:35px;line-height:42px}
  .cta{left:315px;top:202px;width:94px;height:30px;border-radius:15px;
    background:linear-gradient(180deg,#39c9f0,var(--cyan-strong));
    font-family:"Fira Sans",Arial,sans-serif;font-weight:700;font-size:10.5px;
    display:flex;align-items:center;justify-content:center;letter-spacing:.3px}
  .particle-field{left:0;top:205px;width:724px;height:165px;
    background:radial-gradient(ellipse 380px 70px at 50% 60px, rgba(140,180,230,.22), transparent 75%);}

  .section-title{left:0;right:0;text-align:center}
  .section-title--tools{top:326px;font-size:24px}
  .section-title--affiliate{top:747px;font-size:26px}

  /* tool cards */
  .tool-card{width:255px;height:117px;border:1.5px solid var(--cyan);border-radius:58px;display:flex;align-items:center}
  .tool-card--active{background:var(--card-fill)}
  .tool-card__icon{width:60px;flex:none;display:flex;justify-content:center;margin-left:0}
  .tool-card__body{padding-right:10px}
  .tool-card__title{font-family:"Open Sans",Arial,sans-serif;font-weight:600;font-size:10px;line-height:12px;margin-bottom:6px}
  .tool-card ul{list-style:none}
  .tool-card li{position:relative;padding-left:11px;font-size:7px;line-height:12px}
  .tool-card li::before{content:"";position:absolute;left:0;top:4px;width:4px;height:4px;border-radius:50%;background:var(--cyan)}

  .pager{top:660px;left:335px;display:flex;gap:7px}

  /* affiliate grid */
  .affiliate-label{transform:translateX(-50%);text-align:center;font-family:"Fira Sans",Arial,sans-serif;font-weight:600;font-size:10.5px;line-height:13.5px;white-space:nowrap}
  .affiliate-label small{display:block;font-size:6px;line-height:9px;font-weight:700}

  /* footer */
  .footer{left:0;top:1125px;width:724px;height:75px;background:var(--footer)}
  .social{left:261px;top:1153px;display:flex;gap:5.5px}
  .social span{width:21px;height:21px;border-radius:50%;background:var(--white)}
  .legal{left:406px;top:1158px;font-size:8px;color:var(--muted)}
  .legal a{color:var(--muted);text-decoration:none}
</style>
</head>
<body>

  <div class="abs brand brand--top"><span class="brand-mark"></span>Pavlora</div>

  <div class="abs particle-field" role="img" aria-label="Glowing field of particle dots forming a digital wave horizon"></div>

  <h1 class="abs hero-title heading">The <span class="accent">Premier</span><br>AI Website Builder</h1>

  <a class="abs cta" href="https://pavlora.com" style="color:var(--white);text-decoration:none">GET STARTED</a>

  <svg class="abs" style="left:355px;top:262px" width="14" height="30" viewBox="0 0 14 30" aria-hidden="true">
    <rect x="1" y="1" width="12" height="19" rx="6" fill="none" stroke="#fff" stroke-width="1.2"/>
    <line x1="7" y1="5" x2="7" y2="8" stroke="#fff" stroke-width="1.2"/>
    <path d="M7 23v5M5 26l2 2 2-2" fill="none" stroke="#fff" stroke-width=".9"/>
  </svg>

  <h2 class="abs section-title section-title--tools heading"><span class="accent">AI Business</span> Tool</h2>

  <!-- tool cards -->
  <div class="abs tool-card tool-card--active" style="left:100px;top:388px">
    <div class="tool-card__icon">
      <svg width="38" height="38" viewBox="0 0 38 38" fill="none" stroke="#fff" stroke-width="1.3" aria-hidden="true">
        <path d="M17 4c-6 0-9 4-9 8-4 1-6 5-4 9-2 4 1 9 6 9 1 3 4 5 7 4z"/>
        <path d="M17 4v30M21 8h6M21 15h10M21 22h8M21 29h5"/>
        <circle cx="29" cy="8" r="2"/><circle cx="33" cy="15" r="2"/><circle cx="31" cy="22" r="2"/><circle cx="28" cy="29" r="2"/>
      </svg>
    </div>
    <div class="tool-card__body">
      <h3 class="tool-card__title">AI Instant Website Generator</h3>
      <ul>
        <li>Get a professional, SEO-optimized website in seconds!</li>
        <li>Includes custom domain, secure high-speed hosting, professional images, and more!</li>
      </ul>
    </div>
  </div>

  <div class="abs tool-card" style="left:369px;top:388px">
    <div class="tool-card__icon">
      <svg width="40" height="36" viewBox="0 0 40 36" fill="none" stroke="var(--cyan)" stroke-width="1.4" aria-hidden="true">
        <rect x="16" y="8" width="20" height="14" rx="4"/><circle cx="22" cy="15" r="1.5"/><circle cx="30" cy="15" r="1.5"/>
        <path d="M26 8V4"/><circle cx="26" cy="3" r="1.2"/>
        <path d="M14 17H4a2 2 0 0 0-2 2v9a2 2 0 0 0 2 2h2v4l4-4h8a2 2 0 0 0 2-2v-4"/>
        <path d="M7 25h1M11 25h1M15 25h1"/>
      </svg>
    </div>
    <div class="tool-card__body">
      <h3 class="tool-card__title">AI ChatBot</h3>
      <ul>
        <li>Fully-trainable ChatBot will learn about your business to automate the customer support process!</li>
        <li>Built-in CRM features integrate emailing, text messaging, and contact forms!</li>
      </ul>
    </div>
  </div>

  <div class="abs tool-card" style="left:100px;top:519px">
    <div class="tool-card__icon">
      <svg width="36" height="32" viewBox="0 0 36 32" fill="none" stroke="var(--cyan)" stroke-width="1.4" aria-hidden="true">
        <rect x="2" y="2" width="32" height="22" rx="2"/><rect x="5" y="5" width="26" height="16"/>
        <path d="M13 24v4M23 24v4M10 29h16"/>
        <path d="M11 9h2l2 7h8l2-5H14"/><circle cx="16" cy="18" r=".8"/><circle cx="22" cy="18" r=".8"/>
      </svg>
    </div>
    <div class="tool-card__body">
      <h3 class="tool-card__title">Online Store Builder (E-Commerce)<br>with AI Assistance</h3>
      <ul>
        <li>Sell you products online and integrate your products into any website!</li>
        <li>Accept payments from multiple payment gateways including Paynexa and Coinvault!</li>
      </ul>
    </div>
  </div>

  <div class="abs tool-card" style="left:369px;top:519px">
    <div class="tool-card__icon">
      <svg width="40" height="38" viewBox="0 0 40 38" fill="none" stroke="var(--cyan)" stroke-width="1.4" aria-hidden="true">
        <path d="M6 14v18h30V22"/><path d="M2 32h38v2H2z"/>
        <path d="M12 12h16v11H18l-4 4v-4h-2z"/><path d="M15 16h9M15 19h6"/>
        <path d="M28 16l8-12 3 2-8 12-4 1z"/>
      </svg>
    </div>
    <div class="tool-card__body">
      <h3 class="tool-card__title">AI Auto-Blogging System</h3>
      <ul>
        <li>AI will generate an incredible blog for your business in seconds and immediately begin posting content for you!</li>
        <li>Choose from daily, weekly, or monthly automated blog posting. Consistent, unique, SEO-optimized content posting on cruise control!</li>
      </ul>
    </div>
  </div>

  <div class="abs pager" aria-label="Carousel controls">
    <svg width="23" height="23" viewBox="0 0 23 23" fill="none" stroke="#fff" stroke-width="1.5" aria-label="Previous"><circle cx="11.5" cy="11.5" r="10.5"/><path d="M17 11.5H6M10 7l-4.5 4.5L10 16"/></svg>
    <svg width="23" height="23" viewBox="0 0 23 23" fill="none" stroke="#fff" stroke-width="1.5" aria-label="Next"><circle cx="11.5" cy="11.5" r="10.5"/><path d="M6 11.5h11M13 7l4.5 4.5L13 16"/></svg>
  </div>

  <h2 class="abs section-title section-title--affiliate heading"><span class="accent">Affiliate</span> Programs</h2>

  <!-- affiliate diamonds -->
  <svg class="abs" style="left:0;top:800px" width="724" height="290" viewBox="0 800 724 290" aria-hidden="true">
    <defs>
      <linearGradient id="featured" x1="0" y1="0" x2="0" y2="1">
        <stop offset="0" stop-color="#1b84e2"/><stop offset="1" stop-color="#33c6ee"/>
      </linearGradient>
    </defs>
    <g fill="none" stroke="var(--line)" stroke-width="1">
      <polygon points="156,809 225,877 156,946 88,877"/>
      <polygon points="294,809 362,877 294,946 225,877"/>
      <polygon points="431,809 499,877 431,946 362,877"/>
      <polygon points="568,809 637,877 568,946 499,877"/>
      <polygon points="156,946 225,1015 156,1083 88,1015"/>
      <polygon points="294,946 362,1015 294,1083 225,1015"/>
      <polygon points="431,946 499,1015 431,1083 362,1015"/>
      <polygon points="568,946 637,1015 568,1083 499,1015"/>
    </g>
    <polygon points="362,877 431,946 362,1015 294,946" fill="url(#featured)"/>

    <g fill="none" stroke="var(--cyan)" stroke-width="1.3">
      <!-- LLC monitor -->
      <rect x="140" y="839" width="33" height="23" rx="1.5"/><path d="M152 862v4M146 867h20"/>
      <rect x="144" y="844" width="8" height="6"/><rect x="148" y="848" width="6" height="6"/><path d="M158 845h11M158 849h11M158 853h11M150 858h16"/>
      <!-- web design -->
      <rect x="278" y="848" width="10" height="24"/><rect x="290" y="848" width="17" height="24"/>
      <circle cx="298.5" cy="857" r="4"/><path d="M293 866h11M281 852h4M281 857h4M281 862h4"/>
      <!-- search ads: bar chart -->
      <path d="M416 871h30M420 871v-10M428 871v-18M436 871v-26M444 871v-14"/>
      <!-- social -->
      <rect x="553" y="847" width="14" height="14" rx="2"/><path d="M557 850v8M562 850v8M555 852h10M555 856h10"/>
      <rect x="570" y="839" width="14" height="14" rx="2"/><path d="M574 849v-4h3l2-3v7z"/>
      <circle cx="569" cy="866" r="5"/>
      <!-- logo -->
      <circle cx="156" cy="989" r="14"/><circle cx="156" cy="989" r="10"/>
      <path d="M142 975h28M142 1003h28"/>
      <!-- trademark doc -->
      <rect x="281" y="977" width="22" height="30"/><circle cx="291" cy="986" r="5"/><path d="M285 995h14M285 999h14M285 1003h10"/>
      <path d="M301 1000h6v8h-6z"/>
      <!-- patent clipboard -->
      <rect x="416" y="975" width="24" height="32" rx="2"/><path d="M423 975v-3h10v3"/>
      <path d="M421 983h3M426 983h9M421 990h3M426 990h9M421 997h3M426 997h6"/>
      <path d="M440 992l7 3v5c0 4-3 6-7 8-4-2-7-4-7-8v-5z"/><path d="M437 1000l2 2 4-4"/>
      <!-- printer -->
      <path d="M558 984v-9h16l3 3v6"/><rect x="554" y="984" width="29" height="13" rx="2"/>
      <rect x="559" y="993" width="18" height="12"/><path d="M562 998h12M562 1002h12"/><circle cx="579" cy="988" r=".8"/>
    </g>
    <!-- AI chip -->
    <g fill="none" stroke="#fff" stroke-width="1.3">
      <rect x="349" y="910" width="26" height="26" rx="2"/>
      <path d="M353 906v4M358 906v4M363 906v4M368 906v4M371 906v4M353 936v4M358 936v4M363 936v4M368 936v4M371 936v4M345 914h4M345 919h4M345 924h4M345 929h4M375 914h4M375 919h4M375 924h4M375 929h4"/>
    </g>
    <text x="362" y="928" text-anchor="middle" fill="#fff" font-family="Fira Sans, sans-serif" font-size="12" font-weight="600">AI</text>
  </svg>

  <div class="abs affiliate-label" style="left:156px;top:877px">Get Your LLC</div>
  <div class="abs affiliate-label" style="left:294px;top:877px">Website Design<br>&amp; Maintenance</div>
  <div class="abs affiliate-label" style="left:431px;top:877px">Search Ads<br>Management</div>
  <div class="abs affiliate-label" style="left:568px;top:877px">Social Media<br>Posting Service</div>
  <div class="abs affiliate-label" style="left:362px;top:946px">Bulk AI Content<br>Generator</div>
  <div class="abs affiliate-label" style="left:156px;top:1014px">Logo Design</div>
  <div class="abs affiliate-label" style="left:294px;top:1014px">Trademark<br>Registration</div>
  <div class="abs affiliate-label" style="left:431px;top:1014px">Patent Application</div>
  <div class="abs affiliate-label" style="left:568px;top:1014px">Printing Services<small>(including postcards,<br>flyers, and merch.)</small></div>

  <footer class="abs footer"></footer>
  <div class="abs brand brand--footer"><span class="brand-mark"></span>Pavlora</div>
  <div class="abs social" aria-label="Social links"><span></span><span></span><span></span><span></span><span></span></div>
  <p class="abs legal">© 2024 Pavlora. All Rights Reserved &nbsp;|&nbsp; <a href="https://pavlora.com">Privacy</a> &nbsp;|&nbsp; <a href="https://pavlora.com">Terms of use</a></p>

</body>
</html>
```